Consultancy Business Card Design

We need a business card design for a new company based in singapore called KestrelOak. KestrelOak a boutique consultancy firm offering broad-based business solutions, from conception to re-invention, for ventures from new start-ups to long-running traditional businesses.
Its 2 main divisions (Food & Beverage Operations and Construction & Project Management) have access to a wide range of networks, knowledge bases, and resources to service its clients across numerous diverse sectors. This includes, and is not limited to, construction, F&B, and retail.
We are a company that combines the ambition, boldness and energy of one in the 20s with the dedication, level-headedness and dependability of one entering its 30s. Bridging the experiences of the old with ideals of the young, we draw on the positives of both to create a unique synergy.
We hope to see designs that fits our company profile.
Industry/Entity Type
Boutique
Contact Information for Business Card
KestrelOak(Company Name)
Marcus Thiel (Name)
Principle Consultant (Title)
F&B and Hospitality (Division)
(+65) 8043 5617 (Contact no.)
marcus@kestreloak.com.sg (Email)
Colors
Designer to choose colors to be used in the design.

```html
<!DOCTYPE html>
<html lang="en">
<head>
<meta charset="utf-8">
<title>KestrelOak Business Card</title>
<link href="https://fonts.googleapis.com/css2?family=Arimo:wght@400;700&display=swap" rel="stylesheet">
<style>
  :root {
    --page: #e9e6e1;
    --card-black: #000000;
    --card-top: #1d1d1d;
    --card-bottom: #050505;
    --white: #ffffff;
    --brand-blue: #3a7cc4;
    --title-yellow: #e6e62a;
    --division-green: #7cc24a;
    --icon-blue: #7cc8ea;
  }
  * { box-sizing: border-box; margin: 0; padding: 0; }
  html, body {
    width: 1200px; height: 1200px; overflow: hidden;
    background: var(--page);
    font-family: "Arimo", Arial, sans-serif;
  }
  .canvas { position: relative; width: 1200px; height: 1200px; }
  .card {
    position: absolute; left: 150px; width: 900px; height: 555px;
    overflow: hidden; box-shadow: 0 6px 18px rgba(0,0,0,0.25);
  }
  .card--front { top: 36px; background: var(--card-black); }
  .card--back { top: 609px; background: var(--card-top); }
  .wordmark {
    position: absolute; display: flex; align-items: center; gap: 18px;
    color: var(--white); font-weight: 700; font-size: 78px;
    letter-spacing: 2px; line-height: 1; white-space: nowrap;
  }
  .wordmark__square {
    width: 34px; height: 34px; background: var(--brand-blue); flex: none;
  }
  .card--front .wordmark { left: 50%; top: 252px; transform: translateX(-50%); }
  .card--back .wordmark { right: 62px; top: 66px; }
  .back-shape { position: absolute; inset: 0; }
  .contact { position: absolute; left: 51px; top: 296px; color: var(--white); }
  .contact__name { font-size: 41px; font-weight: 400; line-height: 1; }
  .contact__title { margin-top: 20px; font-size: 24px; color: var(--title-yellow); }
  .contact__division { margin-top: 16px; font-size: 24px; color: var(--division-green); }
  .contact__rule { margin-top: 14px; width: 410px; height: 2px; background: var(--white); }
  .contact__line {
    display: flex; align-items: center; gap: 14px;
    font-size: 25px; margin-top: 18px;
  }
  .contact__line:first-of-type { margin-top: 22px; }
  .contact__icon { width: 26px; height: 22px; flex: none; }
</style>
</head>
<body>
<div class="canvas">
  <section class="card card--front">
    <div class="wordmark"><span>KESTRELOAK</span><span class="wordmark__square"></span></div>
  </section>

  <section class="card card--back">
    <svg class="back-shape" viewBox="0 0 900 555" preserveAspectRatio="none">
      <defs>
        <linearGradient id="topShade" x1="0" y1="0" x2="0" y2="1">
          <stop offset="0" stop-color="#1a1a1a"/>
          <stop offset="1" stop-color="#262626"/>
        </linearGradient>
      </defs>
      <rect width="900" height="555" fill="url(#topShade)"/>
      <path d="M0,238 C200,200 450,188 620,246 C760,296 850,378 900,440 L900,555 L0,555 Z" fill="#050505"/>
      <path d="M0,238 C200,200 450,188 620,246 C760,296 850,378 900,440" fill="none" stroke="#333" stroke-width="1.5"/>
    </svg>
    <div class="wordmark"><span>KESTRELOAK</span><span class="wordmark__square"></span></div>
    <div class="contact">
      <div class="contact__name">Marcus Thiel</div>
      <div class="contact__title">Principle Consultant</div>
      <div class="contact__division">F&amp;B and Hospitality (Division)</div>
      <div class="contact__rule"></div>
      <div class="contact__line">
        <svg class="contact__icon" viewBox="0 0 26 22" aria-hidden="true">
          <path d="M2,8 C2,3 24,3 24,8 L24,10 L18,10 L18,7 L8,7 L8,10 L2,10 Z" fill="var(--icon-blue)"/>
          <path d="M7,11 L19,11 L23,20 L3,20 Z" fill="var(--icon-blue)"/>
          <circle cx="13" cy="15.5" r="2.6" fill="#050505"/>
        </svg>
        <span>(+65) 8043 5617</span>
      </div>
      <div class="contact__line">
        <svg class="contact__icon" viewBox="0 0 26 22" aria-hidden="true">
          <rect x="1" y="3" width="24" height="16" fill="var(--icon-blue)"/>
          <path d="M1,3 L13,12 L25,3 M1,19 L10,10 M25,19 L16,10" fill="none" stroke="#050505" stroke-width="1.6"/>
        </svg>
        <span>marcus@kestreloak.com.sg</span>
      </div>
    </div>
  </section>
</div>
</body>
</html>
```